Brintel Works - Fast, Efficient and Gas Mainteance for Domestic, Commercial and Industrial clients

We are in the process of purchasing a new business and would like to get a new logo and business card.
Business is a gas maintenance business that also does new gas installations.
Has been established since 1988.
Services include:
Install all types of gas appliances & equipment inc. hot water units
Maintain / repair / replace all types of gas appliances & equipment

Target Market(s)

Domestic, Commercial and Industrial clients

Industry/Entity Type

Business

Contact Information for Business Card

admin@brintelworks.com.au
07 3918 4726
Brintel Works PTY LTD

Logo Text

Gas Fitting & Plumbing Maintenance Specialists

Font styles to use
Sans Serif

Requirements
Must have
• Logo
• Business name, contact number, email address, web address
• Domestic | Commercial | Industrial Est Since 1988
Nice to have
• Possibly a black card with a flame logo to one side
Should not have
• Spelling errors

```html
<!DOCTYPE html>
<html lang="en">
<head>
<meta charset="utf-8">
<title>Brintel Works – Business Card</title>
<link href="https://fonts.googleapis.com/css2?family=Arimo:wght@400;700&display=swap" rel="stylesheet">
<style>
  :root {
    --backdrop: #d8c7a4;
    --card: #000000;
    --brand-red: #c4161c;
    --text-light: #e6e6e6;
    --text-muted: #b5b5b5;
    --tab: #c8c8c8;
    --icon: #111111;
  }
  * { margin: 0; padding: 0; box-sizing: border-box; }
  html, body {
    width: 1200px; height: 1200px; overflow: hidden;
    background: var(--backdrop);
    font-family: "Arimo", Arial, sans-serif;
  }
  .card {
    position: absolute; left: 190px; width: 854px; height: 474px;
    background: var(--card); border-radius: 32px; overflow: hidden;
  }
  .card--front { top: 100px; }
  .card--back { top: 656px; }

  .wordmark {
    color: var(--brand-red); font-weight: 700; letter-spacing: 2px;
    line-height: 1;
  }
  .card--front .wordmark {
    position: absolute; left: 0; right: 0; top: 186px;
    text-align: center; font-size: 112px;
  }

  .identity { position: absolute; left: 96px; top: 168px; width: 234px; }
  .identity .wordmark { font-size: 56px; text-align: center; }
  .identity__company {
    color: #fff; font-size: 19px; letter-spacing: 0.6px; text-align: center;
    margin-top: 16px; word-spacing: 3px;
  }
  .identity__tagline {
    color: var(--text-muted); font-size: 10.5px; text-align: center;
    margin-top: 16px; white-space: nowrap;
  }

  .contacts {
    position: absolute; right: 84px; top: 134px; list-style: none;
    text-align: right; color: var(--text-light); font-size: 24px;
  }
  .contacts li { height: 52px; line-height: 52px; word-spacing: 3px; white-space: nowrap; }

  .icon-tab {
    position: absolute; right: 0; top: 84px; width: 66px; height: 306px;
    background: var(--tab); border-radius: 20px 0 0 20px;
  }
  .icon-tab__item {
    position: absolute; left: 0; width: 46px; height: 52px;
    border-bottom: 1.5px solid var(--icon);
    display: flex; align-items: center; justify-content: center;
  }
  .icon-tab__item svg { width: 24px; height: 24px; fill: var(--icon); }
</style>
</head>
<body>

<section class="card card--front">
  <div class="wordmark">BRINTEL</div>
</section>

<section class="card card--back">
  <div class="identity">
    <div class="wordmark">BRINTEL</div>
    <p class="identity__company">Brintel Works PTY LTD</p>
    <p class="identity__tagline">Domestic | Commercial | Industrial Est Since 1988</p>
  </div>

  <ul class="contacts">
    <li>Adress 01, Adress, City.</li>
    <li>07 3918 4726</li>
    <li>admin@brintelworks.com.au</li>
    <li>www.brintelworks.com.au</li>
  </ul>

  <div class="icon-tab">
    <div class="icon-tab__item" style="top:46px">
      <svg viewBox="0 0 24 24" aria-label="Address"><path d="M12 3 2 12h3v9h5v-6h4v6h5v-9h3z"/></svg>
    </div>
    <div class="icon-tab__item" style="top:98px">
      <svg viewBox="0 0 24 24" aria-label="Phone"><path d="M6.6 10.8a15 15 0 0 0 6.6 6.6l2.2-2.2a1 1 0 0 1 1-.25 11.4 11.4 0 0 0 3.6.57 1 1 0 0 1 1 1V20a1 1 0 0 1-1 1A17 17 0 0 1 3 4a1 1 0 0 1 1-1h3.5a1 1 0 0 1 1 1c0 1.25.2 2.45.57 3.57a1 1 0 0 1-.25 1z"/></svg>
    </div>
    <div class="icon-tab__item" style="top:150px">
      <svg viewBox="0 0 24 24" aria-label="Email"><path d="M12 2a10 10 0 1 0 5 18.7l-1-1.7A8 8 0 1 1 20 12v1.2c0 1-.7 1.8-1.5 1.8S17 14.2 17 13.2V7h-2v1a5 5 0 1 0 .6 6.9A3.4 3.4 0 0 0 18.5 17c2 0 3.5-1.7 3.5-3.8V12A10 10 0 0 0 12 2zm0 13a3 3 0 1 1 0-6 3 3 0 0 1 0 6z"/></svg>
    </div>
    <div class="icon-tab__item" style="top:202px">
      <svg viewBox="0 0 24 24" aria-label="Website"><path d="M12 2a10 10 0 1 0 0 20 10 10 0 0 0 0-20zm6.9 6h-3a15 15 0 0 0-1.3-3.9A8 8 0 0 1 18.9 8zM12 4c.8 1.2 1.5 2.5 1.9 4h-3.8c.4-1.5 1.1-2.8 1.9-4zM4.3 14a8 8 0 0 1 0-4h3.4a16 16 0 0 0 0 4zm.8 2h3a15 15 0 0 0 1.3 3.9A8 8 0 0 1 5.1 16zm3-8h-3a8 8 0 0 1 4.3-3.9A15 15 0 0 0 8.1 8zM12 20c-.8-1.2-1.5-2.5-1.9-4h3.8c-.4 1.5-1.1 2.8-1.9 4zm2.3-6H9.7a14 14 0 0 1 0-4h4.6a14 14 0 0 1 0 4zm.3 5.9a15 15 0 0 0 1.3-3.9h3a8 8 0 0 1-4.3 3.9zm1.7-5.9a16 16 0 0 0 0-4h3.4a8 8 0 0 1 0 4z"/></svg>
    </div>
  </div>
</section>

</body>
</html>
```